Awesome photographers card for an awesome new business

Double sided business card Black background and silver logo in middle on one side. Details on otherside. please keep it simple

Industry/Entity Type

Photographer

Contact Information for Business Card

Gerald Fenwick
0452817360
GeraldFenwickPhotography47@mailbox.test
www.GeraldFenwickPhotography.test.au
Instagram _Gerald_fenwick

Requirements
Must have
• My logo in Silver
• please use instagram logo instead of "Instagram"

```html
<!DOCTYPE html>
<html lang="en">
<head>
<meta charset="utf-8">
<title>Gerald Fenwick Photography – Business Card</title>
<link rel="stylesheet" href="https://fonts.googleapis.com/css2?family=Oswald:wght@600&family=Questrial&display=swap">
<style>
  :root {
    --canvas: #e9e8e6;
    --card-white: #ffffff;
    --card-black: #1c1d1f;
    --ink: #2a2a2a;
    --text-grey: #5a5a5a;
    --silver-dark: #7d7d7d;
    --silver-mid: #b9b9b9;
    --silver-light: #f1f1f1;
    --icon: #2b2b2b;
  }
  * { box-sizing: border-box; margin: 0; padding: 0; }
  html, body { width: 1200px; height: 911px; overflow: hidden; }
  body {
    background: var(--canvas);
    font-family: "Questrial", sans-serif;
    position: relative;
  }
  .card {
    position: absolute;
    left: 300px;
    width: 600px;
    height: 343px;
    border-radius: 22px;
    overflow: hidden;
    box-shadow: 0 6px 18px rgba(0,0,0,0.18);
  }
  .card--front { top: 90px; background: var(--card-white); }
  .card--back { top: 478px; background: var(--card-black); }

  .silver-band {
    position: absolute;
    left: 0; top: 0;
    width: 390px; height: 112px;
    background: linear-gradient(180deg, var(--silver-dark) 0%, var(--silver-light) 45%, var(--silver-mid) 75%, var(--silver-dark) 100%);
  }
  .holder-name {
    position: absolute;
    left: 44px; top: 40px;
    font-family: "Oswald", sans-serif;
    font-weight: 600;
    font-size: 24px;
    letter-spacing: 0.5px;
    color: var(--ink);
    text-transform: uppercase;
  }
  .brand-mark {
    position: absolute;
    display: flex;
    align-items: center;
    justify-content: center;
    border-radius: 50%;
    text-align: center;
    font-family: "Questrial", sans-serif;
  }
  .card--front .brand-mark {
    left: 330px; top: 2px;
    width: 118px; height: 118px;
    background: var(--card-white);
    border: 3px solid var(--silver-mid);
    color: var(--silver-dark);
    font-size: 15px;
    line-height: 1.2;
  }
  .card--back .brand-mark {
    left: 220px; top: 92px;
    width: 160px; height: 160px;
    border: 3px solid var(--silver-mid);
    color: var(--silver-mid);
    font-size: 20px;
    line-height: 1.2;
  }

  .contact-list {
    position: absolute;
    right: 26px; top: 168px;
    list-style: none;
  }
  .contact-item {
    display: flex;
    justify-content: flex-end;
    align-items: center;
    gap: 10px;
    height: 24px;
    font-size: 13.5px;
    color: var(--text-grey);
  }
  .contact-icon { width: 14px; height: 14px; flex: none; }
</style>
</head>
<body>

  <section class="card card--front" aria-label="Business card front">
    <div class="silver-band"></div>
    <h1 class="holder-name">Gerald Fenwick</h1>
    <div class="brand-mark">Gerald<br>Fenwick</div>

    <ul class="contact-list">
      <li class="contact-item">
        <span>0452817360</span>
        <svg class="contact-icon" viewBox="0 0 14 14" aria-hidden="true">
          <rect width="14" height="14" rx="2" fill="var(--icon)"/>
          <path d="M4 3.2 L5.6 3 L6.3 5 L5.3 5.8 Q6.2 7.8 8.2 8.7 L9 7.7 L11 8.4 L10.8 10 Q7.6 10.6 5.4 8.4 Q3.3 6.2 4 3.2Z" fill="#fff"/>
        </svg>
      </li>
      <li class="contact-item">
        <span>GeraldFenwickPhotography47@mailbox.test</span>
        <svg class="contact-icon" viewBox="0 0 14 14" aria-hidden="true">
          <rect width="14" height="14" rx="2" fill="var(--icon)"/>
          <rect x="3" y="4.2" width="8" height="5.6" fill="none" stroke="#fff" stroke-width="1"/>
          <path d="M3 4.2 L7 7.4 L11 4.2" fill="none" stroke="#fff" stroke-width="1"/>
        </svg>
      </li>
      <li class="contact-item">
        <span>www.GeraldFenwickPhotography.test.au</span>
        <svg class="contact-icon" viewBox="0 0 14 14" aria-hidden="true">
          <rect width="14" height="14" rx="2" fill="var(--icon)"/>
          <circle cx="7" cy="7" r="3.8" fill="none" stroke="#fff" stroke-width="1"/>
          <ellipse cx="7" cy="7" rx="1.6" ry="3.8" fill="none" stroke="#fff" stroke-width="0.9"/>
          <line x1="3.2" y1="7" x2="10.8" y2="7" stroke="#fff" stroke-width="0.9"/>
        </svg>
      </li>
      <li class="contact-item">
        <span>_Gerald_fenwick</span>
        <svg class="contact-icon" viewBox="0 0 14 14" aria-hidden="true">
          <rect width="14" height="14" rx="2" fill="var(--icon)"/>
        </svg>
      </li>
    </ul>
  </section>

  <section class="card card--back" aria-label="Business card back">
    <div class="brand-mark">Gerald<br>Fenwick</div>
  </section>

</body>
</html>
```